Ft Darrow Cider Co needs web page design

Need a web design for a ecommerce website for honey wine. We make honeywine (a dessert type wine made with honey). Our initial product is a standard honey wine and pyment and a cyser. We have all our logos and designs but need to place in web design to reflect our product and ecommerce. We want the file labeled "chatwave cover logo 2" as the banner for the site.

Target Market(s)

People who drink sweeter wines, dessert wine, or non traditional/non-grape wines. Cizer drinkers. 20-60 years old.

Requirements
Must have
• The "bee button" picture as the button image. The "cw cover 2" image as the page banner. Open, bright feel/coloring. Coloring featuring gold, red colors that reflect our logos. PLEASE USE THE CHATWAVE COVER 2 AS OR ON LABEL BANNER TOP OF WEB PAGE. Files 2-3-4 and 5 are our first labels. Those are what will be on bottles when we sale them. This should reflect on web page. We will not use file 8 labels but the graphics could be used on website. There for inspiration.
Nice to have
• Reflect the fonts that are on our logos as close as possible.
Should not have
• Not too much black, red, or honey references. We don't want the page to be too saturated with any of those elements. Not cluttered with imagery.

```html
<!DOCTYPE html>
<html lang="en">
<head>
<meta charset="utf-8">
<title>Ft Darrow Cider Co — Honey Wine</title>
<link rel="stylesheet" href="https://fonts.googleapis.com/css2?family=Cinzel:wght@400;700&family=Open+Sans:wght@400;600&display=swap">
<style>
:root{
  --wine:#86112b;
  --wine-dark:#6a1a3d;
  --gold:#f39a1e;
  --gold-deep:#d9861a;
  --green:#5ea130;
  --ink:#333333;
  --muted:#777777;
  --rule:#e2e2e2;
  --band:#f5f5f5;
  --night:#2b2e36;
  --white:#ffffff;
  --soft:#c9c9c9;
}
*{box-sizing:border-box;margin:0;padding:0}
html,body{width:1200px;height:2849px;overflow:hidden}
body{position:relative;font-family:"Open Sans",sans-serif;color:var(--ink);background:var(--white)}
.abs{position:absolute}
a{color:inherit;text-decoration:none}

.announce{top:0;left:0;width:1200px;height:45px;background:var(--wine);color:var(--white);font-size:13px;text-align:center;line-height:45px}
.announce u{text-decoration:underline}

.brand{left:112px;top:58px;width:186px;text-align:center;font-family:"Cinzel",serif;color:var(--wine)}
.brand-name{font-size:21px;letter-spacing:2px;line-height:1}
.brand-sub{font-size:13px;letter-spacing:5px;color:var(--gold-deep);margin-top:8px;border-top:1px solid var(--gold-deep);padding-top:2px}

.search{left:373px;top:66px;width:375px;height:35px;border:2px solid var(--gold);display:flex}
.search span{flex:1;font-size:12px;color:#555;padding:8px 14px}
.search-btn{width:38px;background:var(--gold);display:flex;align-items:center;justify-content:center}
.account{left:776px;top:72px;font-size:14px;color:var(--muted)}
.account a{padding:0 14px;border-left:1px solid #ccc}
.account a:first-child{padding-left:0;border-left:none}
.cart{left:1062px;top:66px}

.header-rule{left:112px;top:135px;width:977px;height:1px;background:var(--rule)}
.nav{top:145px;left:283px;display:flex;font-size:14.5px;color:#444}
.nav a{margin-right:39px;padding-bottom:10px}
.nav a.active{color:var(--wine);font-weight:600;border-bottom:3px solid var(--wine)}

.hero{top:177px;left:0;width:1200px;height:549px;background:linear-gradient(180deg,#4a3a22 0%,#3a2612 45%,#6b3410 70%,#2a1a0c 100%)}
.hero-kicker{top:288px;left:0;width:1200px;text-align:center;font-family:"Cinzel",serif;font-size:29px;letter-spacing:3px;color:#f1ead8}
.hero-rule{left:269px;width:663px;height:1px;background:rgba(255,255,255,.35)}
.hero-title{top:334px;left:0;width:1200px;text-align:center;font-family:"Cinzel",serif;font-weight:700;font-size:80px;letter-spacing:4px;color:var(--white);line-height:90px}
.hero-sub{top:441px;left:0;width:1200px;text-align:center;font-family:"Cinzel",serif;font-size:31px;letter-spacing:3px;color:#f1ead8}
.shop-btn{left:523px;top:501px;width:153px;height:44px;background:var(--gold);color:var(--white);font-weight:600;font-size:19px;display:flex;align-items:center;justify-content:center;gap:8px}
.bee{display:inline-block;border-radius:50%;background:radial-gradient(circle at 40% 35%,#e8c46a,#a77b25)}
.arrow{top:369px}
.dots{top:690px;left:569px;display:flex;gap:8px}
.dots i{width:10px;height:10px;border-radius:50%;background:rgba(255,255,255,.35)}
.dots i:first-child{background:var(--gold)}

.tile{top:779px;width:302px;height:239px;color:var(--white);text-align:center;font-family:"Cinzel",serif;font-weight:700}
.tile-purple{left:112px;background:var(--wine-dark)}
.tile-green{left:449px;background:var(--green)}
.tile-gold{left:786px;background:var(--gold)}
.tile .t1{margin-top:52px;font-size:18px;letter-spacing:3px}
.tile .t2{margin:12px auto 0;width:186px;border-top:1px solid rgba(255,255,255,.3);border-bottom:1px solid rgba(255,255,255,.3);padding:6px 0;font-size:27px;letter-spacing:3px;white-space:nowrap}
.tile-gold .t2{width:252px;font-size:23px;letter-spacing:2px;padding:8px 0 9px}
.tile .t3{margin-top:10px;font-size:18px;letter-spacing:3px}

.product{top:1075px;width:222px}
.product-img{height:288px}
.sale{position:absolute;top:21px;right:7px;padding:3px 9px;font-size:12px;color:var(--white)}
.product-name{margin-top:24px;font-size:13.5px;line-height:21px;color:#444}
.price{margin-top:14px;font-size:13px;font-weight:600}
.price s{color:#999;font-weight:400;margin-left:9px}
.cart-btn{margin-top:26px;width:121px;height:37px;background:var(--gold);color:var(--white);font-size:13px;font-weight:600;display:flex;align-items:center;justify-content:center;gap:6px}

.featured{top:1593px;left:0;width:1200px;height:512px;background:var(--band)}
.section-title{left:0;width:1200px;text-align:center;font-size:33px;color:#444}
.collection{top:1710px;width:222px}
.collection-img{height:288px}
.collection-name{margin-top:22px;font-size:13.5px;line-height:21px;color:#444}
.collection-name b{font-weight:600;color:var(--muted)}

.newsletter{top:2105px;left:0;width:1200px;height:308px;background:#fafafa}
.news-copy{top:2198px;left:320px;width:560px;text-align:center;font-size:15px;line-height:21px;color:#444}
.news-form{left:321px;top:2287px;width:559px;height:43px;display:flex;border:1px solid #ccc;background:var(--white)}
.news-form span{flex:1;font-size:13px;color:#666;padding:12px 14px}
.news-form .btn{width:150px;background:var(--gold);color:var(--white);font-size:20px;display:flex;align-items:center;justify-content:center;gap:6px;margin:-1px -1px -1px 0}

.footer{top:2413px;left:0;width:1200px;height:260px;background:var(--wine)}
.f-col{top:2459px;color:var(--white)}
.f-col h4{font-weight:400;font-size:16px;margin-bottom:24px;color:var(--white)}
.f-col p{font-size:11.5px;line-height:20.5px;color:var(--white)}
.f-col .post{font-size:16px;font-weight:600;margin-bottom:2px;color:var(--white)}
.f-col .quote{font-size:15px;color:var(--white)}
.f-email{width:229px;height:38px;display:flex;margin-top:17px}
.f-email span{flex:1;background:var(--white);color:#777;font-size:13px;padding:10px 14px}
.f-email i{width:46px;background:var(--gold);display:flex;align-items:center;justify-content:center}
.social{display:flex;gap:14px;margin-top:2px}
.social i{width:20px;height:20px;border-radius:50%;background:var(--white)}

.bottom{top:2673px;left:0;width:1200px;height:176px;background:var(--night)}
.bottom-links{top:2714px;left:0;width:1200px;text-align:center;font-size:11.5px;color:var(--soft)}
.pay{top:2754px;left:494px;display:flex;gap:7px}
.pay i{width:31px;height:19px;background:var(--white);border-radius:2px}
.copy{top:2799px;left:0;width:1200px;text-align:center;font-size:11.5px;color:var(--soft)}
.code{top:2799px;left:1129px;font-size:11.5px;color:var(--soft)}
</style>
</head>
<body>

<div class="abs announce">Featured <u>announcement</u> or <u>promotion</u>!</div>

<div class="abs brand">
  <div class="brand-name">FT DARROW</div>
  <div class="brand-sub">CIDER CO</div>
</div>

<div class="abs search"><span>Search store...</span><div class="search-btn">
  <svg width="16" height="16" viewBox="0 0 16 16" fill="none" stroke="#fff" stroke-width="1.6"><circle cx="7" cy="7" r="5"/><path d="M11 11l4 4"/></svg></div></div>

<div class="abs account"><a>Sign in</a><a>Create account</a><a>Checkout</a></div>
<svg class="abs cart" width="28" height="32" viewBox="0 0 28 32" fill="none" stroke="#888" stroke-width="1.4">
  <rect x="2" y="10" width="24" height="20" rx="2"/><path d="M9 13V7a5 5 0 0 1 10 0v6"/></svg>

<div class="abs header-rule"></div>
<nav class="abs nav">
  <a class="active">Home</a><a>About Us</a><a>Products</a><a>Honey Wine</a><a>Features</a><a>Blog</a><a>Contact Us</a>
</nav>

<div class="abs hero" role="img" aria-label="Photo of honey wine bottles and honey jars on a shelf"></div>
<div class="abs hero-kicker">HONEY WINE</div>
<div class="abs hero-rule" style="top:332px"></div>
<div class="abs hero-title">FT DARROW</div>
<div class="abs hero-rule" style="top:427px"></div>
<div class="abs hero-sub">CIDER CO</div>
<a class="abs shop-btn"><i class="bee" role="img" aria-label="Bee button" style="width:28px;height:28px"></i>Shop Now</a>
<svg class="abs arrow" style="left:42px" width="18" height="36" viewBox="0 0 18 36" fill="none" stroke="#ddd" stroke-width="1.5"><path d="M16 2L2 18l14 16"/></svg>
<svg class="abs arrow" style="left:1126px" width="18" height="36" viewBox="0 0 18 36" fill="none" stroke="#ddd" stroke-width="1.5"><path d="M2 2l14 16L2 34"/></svg>
<div class="abs dots"><i></i><i></i><i></i><i></i></div>

<div class="abs tile tile-purple"><div class="t1">NEW</div><div class="t2">ARRIVALS</div><div class="t3">DAILY</div></div>
<div class="abs tile tile-green"><div class="t1">3 DAYS</div><div class="t2">SAVE 25%</div><div class="t3">ONLY</div></div>
<div class="abs tile tile-gold"><div class="t1">SUMMER</div><div class="t2">STOGIES CLUB</div><div class="t3">ONLY</div></div>

<div class="abs product" style="left:112px">
  <div class="product-img" role="img" aria-label="Pyment bottle" style="background:linear-gradient(#cbc89a,#c4c196)"></div>
  <div class="product-name">Nostrud Exercitation Ullamco Nisi Commodo</div>
  <div class="price">$29.00 USD</div>
  <a class="cart-btn"><i class="bee" style="width:22px;height:22px"></i>Add to Cart</a>
</div>
<div class="abs product" style="left:363px">
  <div class="product-img" role="img" aria-label="Cyser bottle" style="position:relative;background:#c9c1bb"><span class="sale" style="background:var(--gold)">SALE!</span></div>
  <div class="product-name">Numquam Eius Modi Tempora Laboriosam</div>
  <div class="price">$24.00 USD<s>$39.00 USD</s></div>
  <a class="cart-btn"><i class="bee" style="width:22px;height:22px"></i>Add to Cart</a>
</div>
<div class="abs product" style="left:614px">
  <div class="product-img" role="img" aria-label="Honey wine bottle" style="background:#dcd2c6"></div>
  <div class="product-name">Exercitationem Ullam Corporis Aperiam</div>
  <div class="price">$4.00 USD</div>
  <a class="cart-btn"><i class="bee" style="width:22px;height:22px"></i>Add to Cart</a>
</div>
<div class="abs product" style="left:865px">
  <div class="product-img" role="img" aria-label="Pyment bottle" style="position:relative;background:#c9d6dc"><span class="sale" style="background:var(--green)">SALE!</span></div>
  <div class="product-name">Occaecati Cupiditate Non Rerum Assumenda</div>
  <div class="price">$29.00 USD<s>$39.00 USD</s></div>
  <a class="cart-btn"><i class="bee" style="width:22px;height:22px"></i>Add to Cart</a>
</div>

<div class="abs featured"></div>
<h2 class="abs section-title" style="top:1627px;font-weight:400">Our Featured Collections</h2>
<div class="abs collection" style="left:112px"><div class="collection-img" role="img" aria-label="Large jug of pyment" style="background:linear-gradient(#6a5548,#b8684a)"></div><div class="collection-name">Omnis Dolor<br><b>2 items</b></div></div>
<div class="abs collection" style="left:363px"><div class="collection-img" role="img" aria-label="Wine bottle on a table" style="background:linear-gradient(#3a2e24,#6b5a46)"></div><div class="collection-name">On Sale<br><b>2 items</b></div></div>
<div class="abs collection" style="left:614px"><div class="collection-img" role="img" aria-label="Mead bottle in front of stacked firewood" style="background:linear-gradient(#8a6a48,#b89068)"></div><div class="collection-name">Under $10<br><b>2 items</b></div></div>
<div class="abs collection" style="left:865px"><div class="collection-img" role="img" aria-label="Decorated jars with white flowers" style="background:linear-gradient(#d8d2c8,#9a7a3c)"></div><div class="collection-name">Under $25<br><b>4 items</b></div></div>

<div class="abs newsletter" role="img" aria-label="Faint background sketch of grapes and wine glasses"></div>
<h2 class="abs section-title" style="top:2145px;font-weight:400">Subscribe to our newsletter</h2>
<p class="abs news-copy">Enter your email address below to join our mailing list and have our latest news and member-only deals delivered straight to your inbox.</p>
<div class="abs news-form"><span>Email</span><a class="btn"><i class="bee" style="width:24px;height:24px"></i>Subscribe</a></div>

<div class="abs footer"></div>
<div class="abs f-col" style="left:112px;width:210px"><h4>Welcome</h4>
  <p>Our products are inspired by the people and world around us. Beautiful, high quality goods that are designed especially for you. Discover our story and meet the people that make our brand what it is.</p></div>
<div class="abs f-col" style="left:363px;width:230px"><h4>Blog</h4>
  <div class="post">Culpa Qui Officia Deserunt</div>
  <p>Temporibus autem quibusdam et aut officiis debitis aut rerum necessitatibus saepe eveniet ut et voluptates repudiandae sint et molestiae non recusandae..</p>
  <div class="quote">“consectetur, adipisci velit”...</div></div>
<div class="abs f-col" style="left:647px;width:240px"><h4>Newsletter</h4>
  <p>Sign up to stay in the loop. Receive updates, access to exclusive deals, and more.</p>
  <div class="f-email"><span>Email</span><i><svg width="26" height="12" viewBox="0 0 26 12" fill="none" stroke="#fff" stroke-width="1.4"><path d="M0 6h24M19 1l5 5-5 5"/></svg></i></div></div>
<div class="abs f-col" style="left:943px"><h4>Newsletter</h4>
  <div class="social"><i aria-label="chatwave"></i><i aria-label="social link"></i><i aria-label="social link"></i><i aria-label="video link"></i><i aria-label="social link"></i></div></div>

<div class="abs bottom"></div>
<div class="abs bottom-links">Search &nbsp;&nbsp;&nbsp;&nbsp; / &nbsp;&nbsp;&nbsp;&nbsp; Theme Features</div>
<div class="abs pay" aria-label="Accepted payment methods"><i></i><i></i><i></i><i></i><i></i><i></i></div>
<div class="abs copy">© 2021 FT DARROW CIDER CO. All rights reserved.</div>
<div class="abs code">C16</div>

</body>
</html>
```